ultra-minimalist business card

front (black background, matte):

reza t. kovin
writer | photographer
get@rezakovin.com

back (white background, matte):

a picture speaks a thousand words;
a word draws a thousand pictures.

www.rezakovin.com

all text should be small (white or silver - as long as it shows against the black - on the front; black or gray - as long as it shows against the white - on the back).

feel free to get creative in terms of arrangement, alignment, and font type, but remember, the overall style is minimalist, so nothing too fancy, please.

thanks.

```html
<!DOCTYPE html>
<html lang="en">
<head>
<meta charset="utf-8">
<title>reza t. kovin — business card</title>
<link rel="stylesheet" href="https://fonts.googleapis.com/css2?family=Source+Serif+4:opsz,wght@8..60,300;8..60,400&display=swap">
<style>
  :root {
    --backdrop: #e4e4e5;
    --card-front: #1f1f20;
    --card-back: #f2f2f3;
    --ink-light: #ececec;
    --rule-light: #c9c9c9;
    --ink-dark: #222222;
    --ink-muted: #6a6a6a;
    --rule-dark: #4a4a4a;
    --serif: "Source Serif 4", Georgia, serif;
  }
  * { margin: 0; padding: 0; box-sizing: border-box; }
  html, body {
    width: 1028px;
    height: 1200px;
    overflow: hidden;
    background: var(--backdrop);
    font-family: var(--serif);
    font-weight: 300;
  }
  .card {
    position: absolute;
    left: 186px;
    width: 658px;
    height: 366px;
    overflow: hidden;
  }
  .card--front { top: 183px; background: var(--card-front); color: var(--ink-light); }
  .card--back  { top: 630px; background: var(--card-back); color: var(--ink-dark); }

  .card__line { position: absolute; line-height: 1; white-space: nowrap; }

  .name    { left: 429px; top: 246px; font-size: 21px; letter-spacing: 0.06em; }
  .role-frame {
    position: absolute;
    left: 429px; top: 279px;
    width: 240px; height: 35px;
    border: 1px solid var(--rule-light);
    border-right: none;
  }
  .role    { left: 438px; top: 288px; font-size: 18px; letter-spacing: 0.02em; }
  .email   { left: 429px; top: 325px; font-size: 18px; letter-spacing: 0.03em; }

  .quote-open  { left: 36px; top: 24px; font-size: 18.5px; }
  .picture-frame {
    position: absolute;
    left: 35px; top: 60px;
    width: 588px; height: 247px;
    border: 1px solid var(--rule-dark);
  }
  .word-frame {
    position: absolute;
    left: 309px; top: 272px;
    width: 360px; height: 70px;
    border: 1px solid var(--rule-dark);
    border-right: none;
  }
  .quote-close { left: 336px; top: 316px; font-size: 18.5px; }
  .website { left: 36px; top: 327px; font-size: 14px; letter-spacing: 0.04em; color: var(--ink-muted); }
</style>
</head>
<body>
  <section class="card card--front" aria-label="card front">
    <p class="card__line name">reza t. kovin</p>
    <div class="role-frame"></div>
    <p class="card__line role">writer | photographer</p>
    <p class="card__line email">get@rezakovin.com</p>
  </section>

  <section class="card card--back" aria-label="card back">
    <p class="card__line quote-open">a picture speaks a thousand words;</p>
    <div class="picture-frame"></div>
    <div class="word-frame"></div>
    <p class="card__line quote-close">a word draws a thousand pictures.</p>
    <p class="card__line website">www.rezakovin.com</p>
  </section>
</body>
</html>
```